Design the Business card for NetVaultic

Business card required for a professional Cyber Security business.
Company Logo and Icon has already been provided however I would like other options for the logo and icon to compare to. Alternatively, please refine/enhance the image of the logo.icon I have already provided.

If you are going to use the provided logo and icon, I was thinking that the company raised Logo on White background would serve well on the front of the card. See attached. AND, a large company raised stand-alone icon to appear on black background on the back of the card with tagline 'Cyber Risk Management, Governance and Consulting' or 'Cyber Security for your Business' See attached.
Alternatively, provide your own design for the logo and icon.

Target Market(s)

Enterprise, Government, Financial.

Contact Information for Business Card

Tavin Orloweth
Founder and CEO

Email Address
Mobile Number
Website URL
LinkedIn URL

Logo Text

NetVaultic - see attached example of logo

Font styles to use
Other font styles liked:
• Berlin Sans FB

Requirements
Must have
• Clean large and bold icon on the back with tagline.
• Horizontal alignment,
Nice to have
• Round edges.
• Raised Logo/Icon
Should not have
• An unprofessional look and feel.

```html
<!DOCTYPE html>
<html lang="en">
<head>
<meta charset="utf-8">
<title>NetVaultic Business Card</title>
<link rel="stylesheet" href="https://fonts.googleapis.com/css2?family=Varela+Round&family=Roboto:wght@400;500;700&display=swap">
<style>
  :root {
    --page: #3a3430;
    --card: #1c1f23;
    --card-edge: #15171a;
    --emboss: #4a4d52;
    --blue: #1f7fd6;
    --blue-soft: #4e63a8;
    --gold: #e9a620;
    --white: #f2f2f2;
    --rule: #6a6d72;
  }
  * { margin: 0; padding: 0; box-sizing: border-box; }
  html, body { width: 1200px; height: 769px; overflow: hidden; }
  body {
    background: var(--page);
    position: relative;
    font-family: "Roboto", Arial, sans-serif;
  }
  .card {
    position: absolute;
    top: 230px;
    width: 540px;
    height: 309px;
    background: var(--card);
    border-radius: 10px;
    box-shadow: 0 6px 18px rgba(0,0,0,.45);
    overflow: hidden;
  }
  .card-back { left: 40px; }
  .card-front { left: 620px; }

  /* back */
  .back-brand {
    position: absolute;
    left: 92px; top: 98px;
    display: flex; align-items: center; gap: 16px;
  }
  .back-brand .mark {
    width: 62px; height: 62px; border-radius: 50%;
    background: var(--emboss);
  }
  .back-brand .name {
    font-family: "Varela Round", Arial, sans-serif;
    font-size: 50px; color: var(--emboss);
  }
  .tagline {
    position: absolute;
    left: 0; right: 0; top: 210px;
    text-align: center;
    font-family: "Varela Round", Arial, sans-serif;
    font-size: 17px;
  }
  .tagline .lead { color: var(--blue-soft); }
  .tagline .rest { color: var(--gold); }

  /* front */
  .front-brand {
    position: absolute;
    left: 30px; top: 128px;
    display: flex; align-items: center; gap: 10px;
  }
  .front-brand .mark {
    width: 44px; height: 44px; border-radius: 50%;
    background: var(--blue);
  }
  .front-brand .name {
    font-family: "Varela Round", Arial, sans-serif;
    font-size: 32px; color: var(--blue);
  }
  .divider {
    position: absolute;
    left: 282px; top: 78px;
    width: 1px; height: 152px;
    background: var(--rule);
  }
  .contact {
    position: absolute;
    left: 302px; top: 92px;
  }
  .person {
    font-size: 19px; font-weight: 700; color: var(--blue);
    text-transform: uppercase; letter-spacing: .3px;
  }
  .role {
    font-size: 15px; font-weight: 700; color: var(--gold);
    text-transform: uppercase; margin-bottom: 12px;
  }
  .details { list-style: none; }
  .details li {
    display: flex; align-items: center; gap: 8px;
    font-size: 14px; color: var(--white);
    line-height: 22px;
  }
  .details svg { width: 13px; height: 13px; flex: none; }
</style>
</head>
<body>

  <section class="card card-back">
    <div class="back-brand">
      <span class="mark"></span>
      <span class="name">NetVaultic</span>
    </div>
    <p class="tagline"><span class="lead">Cyber Risk Management,</span> <span class="rest">Governance &amp; Consulting</span></p>
  </section>

  <section class="card card-front">
    <div class="front-brand">
      <span class="mark"></span>
      <span class="name">NetVaultic</span>
    </div>
    <div class="divider"></div>
    <div class="contact">
      <p class="person">Tavin Orloweth</p>
      <p class="role">Founder &amp; CEO</p>
      <ul class="details">
        <li>
          <svg viewBox="0 0 13 13"><rect x="3" y="0.5" width="7" height="12" rx="1.5" fill="none" stroke="#1f7fd6" stroke-width="1.4"/><circle cx="6.5" cy="10.3" r="0.8" fill="#1f7fd6"/></svg>
          555 014 2290
        </li>
        <li>
          <svg viewBox="0 0 13 13"><rect x="0.5" y="2.5" width="12" height="8" rx="1" fill="#1f7fd6"/><path d="M1 3 L6.5 7.5 L12 3" fill="none" stroke="#1c1f23" stroke-width="1.2"/></svg>
          tavin@netvaultic.com
        </li>
        <li>
          <svg viewBox="0 0 13 13"><circle cx="6.5" cy="6.5" r="6" fill="#1f7fd6"/><path d="M0.5 6.5 H12.5 M6.5 0.5 C3.5 4 3.5 9 6.5 12.5 M6.5 0.5 C9.5 4 9.5 9 6.5 12.5" fill="none" stroke="#1c1f23" stroke-width="1"/></svg>
          www.netvaultic.com
        </li>
        <li>
          <svg viewBox="0 0 13 13"><circle cx="6.5" cy="6.5" r="6" fill="#1f7fd6"/></svg>
          netvaultic
        </li>
      </ul>
    </div>
  </section>

</body>
</html>
```